Business card for Luxury Portable Restroom Trailer company

We are a Luxury Portable Restroom Trailer Company Called FALCRIDGE HIRES. Based in Orange County California. We provide portable restroom trailers for events, such as, Weddings, Concerts, Charity events, Sporting events, Tournaments, Corporate events, ect. We rent and Sell the Luxury restrooms. Our colors are white, grey, and Orange. As you will see in the logo we uploaded.
There are 2 people in the company so the names and titles will change for the 3 people but card will remain the same. Here is the information for each Person: Dwight Penner CFO 555 318-0476
next Person: Leon Marchetti VP 555 318-0476
Next Person: Owen Marchetti CEO 555 318-0476
Information to include on the card: Luxury Restroom Trailers Rental and Sales. Weddings, Concerts, Charity, Sporting and Corp. Events.

```html
<!DOCTYPE html>
<html lang="en">
<head>
<meta charset="UTF-8">
<title>Falcridge Hires – Business Card</title>
<link href="https://fonts.googleapis.com/css2?family=Montserrat:wght@400;500;700;800&display=swap" rel="stylesheet">
<style>
  :root {
    --bg: #1b1b1b;
    --card: #262626;
    --card-deep: #1f1f1f;
    --orange: #f26a21;
    --white: #ffffff;
    --grey: #b9b9b9;
    --emboss: #2e2e2e;
    --emboss-edge: #383838;
  }
  * { margin: 0; padding: 0; box-sizing: border-box; }
  html, body { width: 1200px; height: 801px; overflow: hidden; }
  body {
    background: var(--bg);
    font-family: "Montserrat", sans-serif;
    display: flex;
    align-items: center;
    justify-content: center;
    gap: 48px;
  }
  .card {
    position: relative;
    width: 540px;
    height: 310px;
    background: linear-gradient(160deg, var(--card) 0%, var(--card-deep) 100%);
    border-bottom: 3px solid var(--orange);
    border-left: 2px solid var(--orange);
    overflow: hidden;
  }

  /* Front */
  .brand-emblem {
    position: absolute;
    right: -40px;
    top: -70px;
    width: 270px;
    height: 270px;
  }
  .brand {
    position: absolute;
    left: 34px;
    top: 34px;
    display: flex;
    align-items: center;
    gap: 10px;
  }
  .brand-mark {
    width: 16px;
    height: 16px;
    background: var(--orange);
  }
  .brand-name {
    font-weight: 800;
    font-size: 24px;
    letter-spacing: 1px;
    color: var(--orange);
  }
  .person {
    position: absolute;
    left: 34px;
    top: 96px;
  }
  .person-name {
    font-weight: 800;
    font-size: 22px;
    letter-spacing: 1px;
    color: var(--orange);
    text-transform: uppercase;
  }
  .person-title {
    font-weight: 400;
    font-size: 14px;
    color: var(--white);
    margin-top: 2px;
  }
  .contact {
    position: absolute;
    left: 34px;
    top: 158px;
    list-style: none;
  }
  .contact li {
    display: flex;
    align-items: center;
    gap: 8px;
    font-size: 13px;
    color: var(--white);
    line-height: 22px;
  }
  .contact svg { width: 11px; height: 11px; fill: var(--orange); flex: none; }
  .divider {
    position: absolute;
    left: 34px;
    top: 234px;
    width: 360px;
    height: 1px;
    background: var(--orange);
  }
  .services {
    position: absolute;
    left: 34px;
    top: 244px;
  }
  .services-headline {
    font-size: 13px;
    font-weight: 500;
    color: var(--orange);
  }
  .services-list {
    font-size: 13px;
    color: var(--white);
    margin-top: 4px;
  }

  /* Back */
  .card-back {
    display: flex;
    align-items: center;
    justify-content: center;
  }
  .back-brand {
    display: flex;
    align-items: center;
    gap: 14px;
  }
  .back-brand .brand-mark {
    width: 24px;
    height: 24px;
    background: var(--emboss-edge);
  }
  .back-brand-name {
    font-weight: 800;
    font-size: 40px;
    letter-spacing: 2px;
    color: #3a3a3a;
  }
</style>
</head>
<body>

  <section class="card card-front">
    <svg class="brand-emblem" viewBox="0 0 270 270" role="img" aria-label="Large embossed brand emblem">
      <circle cx="135" cy="135" r="130" fill="var(--emboss)" stroke="var(--emboss-edge)" stroke-width="4"/>
    </svg>

    <div class="brand">
      <span class="brand-mark"></span>
      <span class="brand-name">FALCRIDGE HIRES</span>
    </div>

    <div class="person">
      <p class="person-name">Owen Marchetti</p>
      <p class="person-title">CEO</p>
    </div>

    <ul class="contact">
      <li>
        <svg viewBox="0 0 24 24"><path d="M6.6 10.8a15 15 0 0 0 6.6 6.6l2.2-2.2a1 1 0 0 1 1-.25 11.4 11.4 0 0 0 3.6.57 1 1 0 0 1 1 1V20a1 1 0 0 1-1 1A17 17 0 0 1 3 4a1 1 0 0 1 1-1h3.5a1 1 0 0 1 1 1c0 1.25.2 2.45.57 3.6a1 1 0 0 1-.25 1z"/></svg>
        555 318-0476
      </li>
      <li>
        <svg viewBox="0 0 24 24"><path d="M2 5h20v14H2z M2 5l10 8 10-8" fill="var(--orange)"/><path d="M3 6l9 7 9-7" fill="none" stroke="var(--card)" stroke-width="2"/></svg>
        owen@falcridgehires.com
      </li>
      <li>
        <svg viewBox="0 0 24 24"><circle cx="12" cy="12" r="10"/><path d="M2 12h20M12 2c3 3 3 17 0 20M12 2c-3 3-3 17 0 20" fill="none" stroke="var(--card)" stroke-width="1.5"/></svg>
        www.falcridgehires.com
      </li>
    </ul>

    <div class="divider"></div>

    <div class="services">
      <p class="services-headline">Luxury Restroom Trailers Rental and Sales</p>
      <p class="services-list">Weddings | Concerts | Charity | Sporting | Corp</p>
    </div>
  </section>

  <section class="card card-back">
    <div class="back-brand">
      <span class="brand-mark"></span>
      <span class="back-brand-name">FALCRIDGE HIRES</span>
    </div>
  </section>

</body>
</html>
```